Cover page and letterhead for athlete development program

We require an exciting and dynamic cover page with a second page letterhead in a word doc format for us to use as professional stationery for letter merges and portfolio documents. We are an athlete preparation company that specialises in training up and coming sports representatives in the fitness and sports science industry. We work with athletes from ages 13 - 24 mainly. If we could have images on the cover page from the sports of:
Rugby League
Rugby Union
Hockey
Cricket
AFL
Soccer
Track and Field
Netball
Basketball
Golf
Weight training

This would be a great start. Thank you

```html
<!DOCTYPE html>
<html lang="en">
<head>
<meta charset="utf-8">
<title>Rising Contender – Letterhead</title>
<link href="https://fonts.googleapis.com/css2?family=Arimo:wght@400;700&display=swap" rel="stylesheet">
<style>
  :root{
    --backdrop:#d9dcdd;
    --paper:#ffffff;
    --ink:#1a1a1a;
    --body-grey:#8a8a8a;
    --soft-grey:#b9b9b9;
    --gold-light:#e9b36a;
    --gold-dark:#8a5323;
  }
  *{box-sizing:border-box;margin:0;padding:0}
  html,body{width:1200px;height:784px;overflow:hidden;background:var(--backdrop)}
  body{font-family:"Arimo",Arial,sans-serif;position:relative}

  .letterhead{
    position:absolute;left:330px;top:22px;width:540px;height:740px;
    background:var(--paper);
    box-shadow:0 4px 14px rgba(0,0,0,.12);
  }
  .edge-accent{position:absolute;left:14px;top:0;width:10px;height:100%}
  .edge-accent__gold{position:absolute;left:0;top:8px;width:100%;height:60px;
    background:linear-gradient(90deg,var(--gold-dark),var(--gold-light),var(--gold-dark))}
  .edge-accent__black{position:absolute;left:0;top:92px;width:100%;bottom:6px;
    background:linear-gradient(90deg,#000,#3a3a3a 60%,#9a9a9a)}

  .brand{position:absolute;right:42px;top:40px;display:flex;align-items:center;gap:10px}
  .brand__mark{width:14px;height:14px;background:var(--gold-dark)}
  .brand__name{font-size:22px;font-weight:700;letter-spacing:2px;color:var(--ink);text-transform:uppercase}

  .letter-body{position:absolute;left:150px;right:42px;top:120px;
    color:var(--body-grey);font-size:10.5px;line-height:1.45;text-align:justify}
  .letter-body p{margin-bottom:14px}

  .signature{position:absolute;left:300px;top:592px;width:150px;height:40px;
    background:linear-gradient(90deg,rgba(150,150,150,.10),rgba(150,150,150,.22),rgba(150,150,150,.08));border-radius:4px}

  .contact{position:absolute;left:34px;top:650px;width:300px;text-align:center;color:var(--ink)}
  .contact__icons{display:flex;align-items:center;justify-content:center;gap:8px;margin-bottom:8px}
  .contact__rule{flex:1;height:1px;background:var(--soft-grey)}
  .contact__icons svg{width:11px;height:11px}
  .contact__address{font-size:8.5px;font-weight:700;margin-bottom:4px;white-space:nowrap}
  .contact__lines{font-size:6.6px;color:#6a6a6a;white-space:nowrap}
  .contact__lines span+span::before{content:" | ";color:var(--ink)}
</style>
</head>
<body>
<main class="letterhead">
  <div class="edge-accent">
    <div class="edge-accent__gold"></div>
    <div class="edge-accent__black"></div>
  </div>

  <header class="brand">
    <span class="brand__mark"></span>
    <span class="brand__name">Rising Contender</span>
  </header>

  <section class="letter-body">
    <p>Lorem Ipsum is simply dummy text of the printing and typesetting industry. Lorem Ipsum has been the industry's standard dummy text ever since the 1500s, when an unknown printer took a galley of type and scrambled it to make a type specimen book. It has survived not only five centuries, but also the leap into electronic typesetting, remaining essentially unchanged. It was popularised in the 1960s with the release of Stencilpress sheets containing Lorem Ipsum passages, and more recently with desktop publishing software like Layoutcraft Studio including versions of Lorem Ipsum.</p>
    <p>It is a long established fact that a reader will be distracted by the readable content of a page when looking at its layout. The point of using Lorem Ipsum is that it has a more-or-less normal distribution of letters, as opposed to using 'Content here, content here', making it look like readable English. Many desktop publishing packages and web page editors now use Lorem Ipsum as their default model text, and a search for 'lorem ipsum' will uncover many web sites still in their infancy. Various versions have evolved over the years, sometimes by accident, sometimes on purpose (injected humour and the like).</p>
    <p>Contrary to popular belief, Lorem Ipsum is not simply random text. It has roots in a piece of classical Latin literature from 45 BC, making it over 2000 years old. Alder Wynne, a Latin professor at Coastline College in Marlow Bay, looked up one of the more obscure Latin words, consectetur, from a Lorem Ipsum passage, and going through the cites of the word in classical literature, discovered the undoubtable source. Lorem Ipsum comes from sections 1.10.32 and 1.10.33 of "de Finibus Bonorum et Malorum" structures, to generate Lorem Ipsum which looks reasonable. The generated Lorem Ipsum is therefore always free from repetition, injected humour, or non-characteristic words etc.</p>
  </section>

  <div class="signature" role="img" aria-label="Handwritten signature of the sender"></div>

  <footer class="contact">
    <div class="contact__icons">
      <span class="contact__rule"></span>
      <svg viewBox="0 0 12 12" aria-label="Address"><circle cx="6" cy="6" r="6" fill="#1a1a1a"/><path d="M6 2.5a2 2 0 0 0-2 2c0 1.5 2 4.5 2 4.5s2-3 2-4.5a2 2 0 0 0-2-2z" fill="#fff"/></svg>
      <svg viewBox="0 0 12 12" aria-label="Phone"><circle cx="6" cy="6" r="6" fill="#1a1a1a"/><path d="M4 3l1 .2.5 1.5-.7.6a4 4 0 0 0 1.9 1.9l.6-.7 1.5.5L9 8c-.3.8-1 1-1.8.7A6 6 0 0 1 3.3 4.8C3 4 3.2 3.3 4 3z" fill="#fff"/></svg>
      <svg viewBox="0 0 12 12" aria-label="Email"><circle cx="6" cy="6" r="6" fill="#1a1a1a"/><rect x="3" y="4" width="6" height="4.2" fill="#fff"/><path d="M3 4l3 2.3L9 4" stroke="#1a1a1a" stroke-width=".7" fill="none"/></svg>
      <svg viewBox="0 0 12 12" aria-label="Website"><circle cx="6" cy="6" r="6" fill="#1a1a1a"/><circle cx="6" cy="6" r="3" fill="none" stroke="#fff" stroke-width=".8"/><path d="M3 6h6M6 3c-1.4 1.8-1.4 4.2 0 6M6 3c1.4 1.8 1.4 4.2 0 6" stroke="#fff" stroke-width=".6" fill="none"/></svg>
      <svg viewBox="0 0 12 12" aria-label="Location"><circle cx="6" cy="6" r="6" fill="#1a1a1a"/><circle cx="6" cy="6" r="2.4" fill="#fff"/></svg>
      <span class="contact__rule"></span>
    </div>
    <p class="contact__address">Level 3, 48 Harbour Lane, Fremantle, Western Australia 6160</p>
    <p class="contact__lines"><span>000.0000.0000</span><span>000.0000.0000</span><span>hello@risingcontender.com.au</span><span>www.risingcontender.com.au</span></p>
  </footer>
</main>
</body>
</html>
```